Redesign of the UI of a customer service platform

To improve the user experience of our customers, we need a new design for our agent interface of our customer service platform (velorant.com).
The focus will be on the dashboard and the inbox screens (see attached) along with the common UI elements (Buttons, menu, fonts, forms...)
We want a simple and distinctive design

Target Market(s)

Worldwide

Industry/Entity Type

It Service

Number of Pages Required

3 page

Font styles to use
Sans Serif

Requirements
Must have
• New Onboarding page: this is a new page that is shown to user the first time they login to the platform. This will replace the current onboarding screen (setup SMS, Setup widget...etc)
• Dashboard page: to access important information and activate services (see screenshot from current site)
• Inbox page: to manage all the interactions with customers. (see screenshot from current site)
• UI elements (buttons, menus, forms, tables, fonts, color palette)

```html
<!DOCTYPE html>
<html lang="en">
<head>
<meta charset="utf-8">
<title>Quillora – Get Started</title>
<link rel="stylesheet" href="https://fonts.googleapis.com/css2?family=Lato:wght@400;700&display=swap">
<style>
  :root {
    --brand: #f15a24;
    --bg: #f1f1f1;
    --white: #ffffff;
    --ink: #444444;
    --muted: #8a8a8a;
    --icon: #b5b5b5;
    --divider: #e6e6e6;
    --alert: #e8261c;
    --warn: #f7b500;
    --online: #3cb64a;
    --track: #d8d8d8;
  }
  * { box-sizing: border-box; margin: 0; padding: 0; }
  html, body { width: 1200px; height: 831px; overflow: hidden; }
  body {
    position: relative;
    background: var(--bg);
    font-family: "Lato", sans-serif;
    color: var(--ink);
  }
  .topbar {
    position: absolute; left: 0; top: 0; width: 1200px; height: 83px;
    background: var(--white); display: flex;
  }
  .brand-tile {
    width: 83px; height: 83px; background: var(--brand);
    display: flex; align-items: center; justify-content: center;
    color: var(--white); font-size: 13px; font-weight: 700; letter-spacing: .3px;
  }
  .nav { display: flex; }
  .nav-item {
    position: relative; width: 84px; height: 83px;
    border-right: 1px solid var(--divider);
    display: flex; flex-direction: column; align-items: center; justify-content: flex-end;
    padding-bottom: 16px; font-size: 13px; color: var(--muted);
  }
  .nav-item svg { position: absolute; top: 15px; left: 28px; }
  .badge {
    position: absolute; top: 17px; left: 50px; width: 24px; height: 24px; border-radius: 50%;
    color: var(--white); font-size: 12px; font-weight: 700;
    display: flex; align-items: center; justify-content: center;
  }
  .badge--alert { background: var(--alert); }
  .badge--warn { background: var(--warn); }
  .avatar {
    position: absolute; right: 14px; top: 14px; width: 56px; height: 56px; border-radius: 50%;
    background: radial-gradient(circle at 50% 40%, #c9a58a, #6c5a4c 60%, #dfe3e6 62%);
  }
  .status-dot {
    position: absolute; right: 62px; top: 15px; width: 14px; height: 14px; border-radius: 50%;
    background: var(--online); border: 2px solid var(--white);
  }
  .page-title {
    position: absolute; top: 122px; width: 1200px; text-align: center;
    font-size: 28px; font-weight: 400; color: var(--ink);
  }
  .video {
    position: absolute; left: 344px; top: 196px; width: 513px; height: 299px;
    background: linear-gradient(135deg, #8a5a3e 0%, #d9b894 35%, #f0e6d4 55%, #a07356 80%, #4a3124 100%);
  }
  .play-button {
    position: absolute; left: 221px; top: 114px; width: 70px; height: 70px; border-radius: 50%;
    background: rgba(255,255,255,.85);
    display: flex; align-items: center; justify-content: center;
  }
  .player-bar {
    position: absolute; left: 344px; top: 509px; width: 513px; height: 16px;
    display: flex; align-items: center; font-size: 11px; color: #a0a0a0;
  }
  .player-bar .time { margin-left: 8px; width: 26px; }
  .track { position: relative; flex: 1; height: 3px; background: var(--track); margin-left: 10px; }
  .track-fill { position: absolute; left: 0; top: 0; width: 50%; height: 3px; background: var(--brand); }
  .section-title {
    position: absolute; top: 572px; width: 1200px; text-align: center;
    font-size: 20px; font-weight: 400; color: var(--ink);
  }
  .addon {
    position: absolute; top: 650px; width: 140px; margin-left: -70px; text-align: center;
  }
  .addon-icon { height: 76px; display: flex; align-items: center; justify-content: center; position: relative; }
  .addon-wordmark { font-size: 20px; font-weight: 700; color: var(--icon); }
  .addon-check { position: absolute; left: 27px; top: 0; }
  .addon-name { margin-top: 22px; font-size: 19px; color: var(--ink); }
  .watch-link {
    margin-top: 12px; font-size: 13px; color: var(--brand);
    display: flex; align-items: center; justify-content: center; gap: 5px;
  }
</style>
</head>
<body>
  <header class="topbar">
    <div class="brand-tile">Quillora</div>
    <nav class="nav">
      <div class="nav-item">
        <svg width="28" height="26" viewBox="0 0 28 26"><path d="M2 14h7l2 4h6l2-4h7v10H2z" fill="#b5b5b5"/><path d="M14 2v9M10 7l4 4 4-4" stroke="#b5b5b5" stroke-width="2" fill="none"/></svg>
        <span class="badge badge--alert">4</span>Inbox
      </div>
      <div class="nav-item">
        <svg width="28" height="28" viewBox="0 0 28 28"><rect x="3" y="3" width="18" height="22" fill="none" stroke="#b5b5b5" stroke-width="2"/><path d="M7 9h10M7 13h10M7 17h6" stroke="#b5b5b5" stroke-width="2"/></svg>
        <span class="badge badge--warn">1</span>Tasks
      </div>
      <div class="nav-item">
        <svg width="28" height="28" viewBox="0 0 28 28"><circle cx="14" cy="9" r="6" fill="#b5b5b5"/><path d="M3 27c0-8 5-11 11-11s11 3 11 11z" fill="#b5b5b5"/></svg>
        Customers
      </div>
      <div class="nav-item">
        <svg width="30" height="26" viewBox="0 0 30 26"><path d="M2 3l26 10L2 23l4-10z M6 13h22" fill="none" stroke="#b5b5b5" stroke-width="2" stroke-linejoin="round"/></svg>
        Campaigns
      </div>
      <div class="nav-item">
        <svg width="28" height="28" viewBox="0 0 28 28"><text x="8" y="22" font-family="Lato, sans-serif" font-size="24" fill="#b5b5b5">$</text></svg>
        Payments
      </div>
      <div class="nav-item">
        <svg width="28" height="28" viewBox="0 0 28 28"><path d="M3 26V4M10 26V10M17 26V6M24 26V14" stroke="#b5b5b5" stroke-width="3"/></svg>
        Reports
      </div>
      <div class="nav-item">
        <svg width="28" height="28" viewBox="0 0 28 28"><circle cx="14" cy="14" r="8" fill="none" stroke="#b5b5b5" stroke-width="5" stroke-dasharray="4 2.3"/><circle cx="14" cy="14" r="6" fill="#b5b5b5"/><circle cx="14" cy="14" r="3" fill="#fff"/></svg>
        Settings
      </div>
    </nav>
    <span class="status-dot"></span>
    <div class="avatar" role="img" aria-label="Agent profile photo"></div>
  </header>

  <h1 class="page-title">Get Started</h1>

  <div class="video" role="img" aria-label="Video still: a team working together over papers on a sunny office desk">
    <div class="play-button">
      <svg width="20" height="22" viewBox="0 0 20 22"><path d="M2 1l17 10L2 21z" fill="#f15a24"/></svg>
    </div>
  </div>
  <div class="player-bar">
    <svg width="10" height="10" viewBox="0 0 10 10"><path d="M1 0l8 5-8 5z" fill="#a0a0a0"/></svg>
    <span class="time">0:00</span>
    <div class="track"><div class="track-fill"></div></div>
  </div>

  <h2 class="section-title">Select Your Add-ons</h2>

  <div class="addon" style="left:276px">
    <div class="addon-icon">
      <svg width="68" height="62" viewBox="0 0 68 62"><rect x="2" y="2" width="64" height="44" rx="3" fill="none" stroke="#b5b5b5" stroke-width="4"/><rect x="8" y="8" width="52" height="32" fill="#b5b5b5"/><path d="M26 48l-2 10h20l-2-10z" fill="#b5b5b5"/><rect x="16" y="57" width="36" height="4" fill="#b5b5b5"/></svg>
    </div>
    <div class="addon-name">Campaigns</div>
    <div class="watch-link"><svg width="12" height="12" viewBox="0 0 12 12"><circle cx="6" cy="6" r="5" fill="none" stroke="#f15a24" stroke-width="1.3"/><path d="M5 3.5l2.5 2.5L5 8.5" fill="none" stroke="#f15a24" stroke-width="1.3"/></svg>Watch Video</div>
  </div>

  <div class="addon" style="left:438px">
    <div class="addon-icon"><span class="addon-wordmark">Friendnet</span></div>
    <div class="addon-name">Messenger</div>
    <div class="watch-link"><svg width="12" height="12" viewBox="0 0 12 12"><circle cx="6" cy="6" r="5" fill="none" stroke="#f15a24" stroke-width="1.3"/><path d="M5 3.5l2.5 2.5L5 8.5" fill="none" stroke="#f15a24" stroke-width="1.3"/></svg>Watch Video</div>
  </div>

  <div class="addon" style="left:599px">
    <div class="addon-icon">
      <svg width="66" height="62" viewBox="0 0 66 62"><path d="M33 4c17 0 31 11 31 25S50 54 33 54c-4 0-8-1-12-2L5 60l6-12C5 43 2 36 2 29 2 15 16 4 33 4z" fill="#b5b5b5"/><path d="M20 22h26M20 30h26M20 38h18" stroke="#fff" stroke-width="2.5"/></svg>
      <svg class="addon-check" width="27" height="27" viewBox="0 0 27 27"><circle cx="13.5" cy="13.5" r="12.5" fill="#3cb64a"/><path d="M7.5 14l4 4 8-9" fill="none" stroke="#fff" stroke-width="3"/></svg>
    </div>
    <div class="addon-name">SMS</div>
    <div class="watch-link"><svg width="12" height="12" viewBox="0 0 12 12"><circle cx="6" cy="6" r="5" fill="none" stroke="#f15a24" stroke-width="1.3"/><path d="M5 3.5l2.5 2.5L5 8.5" fill="none" stroke="#f15a24" stroke-width="1.3"/></svg>Watch Video</div>
  </div>

  <div class="addon" style="left:761px">
    <div class="addon-icon"><span class="addon-wordmark">Paperwing</span></div>
    <div class="addon-name">Paperwing</div>
    <div class="watch-link"><svg width="12" height="12" viewBox="0 0 12 12"><circle cx="6" cy="6" r="5" fill="none" stroke="#f15a24" stroke-width="1.3"/><path d="M5 3.5l2.5 2.5L5 8.5" fill="none" stroke="#f15a24" stroke-width="1.3"/></svg>Watch Video</div>
  </div>

  <div class="addon" style="left:922px">
    <div class="addon-icon">
      <svg width="40" height="66" viewBox="0 0 40 66"><text x="1" y="56" font-family="Lato, sans-serif" font-size="62" fill="#b5b5b5">$</text></svg>
    </div>
    <div class="addon-name">Payment</div>
    <div class="watch-link"><svg width="12" height="12" viewBox="0 0 12 12"><circle cx="6" cy="6" r="5" fill="none" stroke="#f15a24" stroke-width="1.3"/><path d="M5 3.5l2.5 2.5L5 8.5" fill="none" stroke="#f15a24" stroke-width="1.3"/></svg>Watch Video</div>
  </div>
</body>
</html>
```